Compelling Recycling & Environmental Product Awareness

Create a FB page design to engage target audiences that want to learn about plastic recycling facts and information. The product is expanded polystyrene (EPS) packaging which is highly recyclable while a majority of the public believes otherwise. We are looking to improve our credibility and increase traffic to our FB page. See https://www.facebook.com/FoamLoopHub/

Target Market(s)

Primarily women ages 33-44; currently 68% of our current FB activity.

Industry/Entity Type

Plastic packaging industry.

Font styles to use
Sans Serif

Colors
0054AA
0677BA
7BADD7
CADEEF
E8F1F8
59FF00
82FF00
B8FF75
E3FFCB
F4FFEA
F0912C
F2A743
F7CA91
FBE8D2
FDF5EE

Requirements
Must have
• Visual engagement that promotes a persuasive presentation.
Should not have
• No hype.

```html
<!DOCTYPE html>
<html lang="en">
<head>
<meta charset="utf-8">
<title>FoamLoop Recycling Hub</title>
<link rel="stylesheet" href="https://fonts.googleapis.com/css2?family=Inter:wght@400;500;600;700&display=swap">
<style>
:root{
  --page-bg:#f0f2f5;
  --surface:#ffffff;
  --ink:#050505;
  --ink-soft:#65676b;
  --link:#216fdb;
  --action:#1b74e4;
  --rule:#dadde1;
  --chip:#e4e6eb;
  --brand-gold:#b58d1c;
  --brand-olive:#9ca51e;
  --brand-orange:#f2a743;
  --brand-blue:#0677ba;
  --brand-navy:#0054aa;
  --foam:#e8f1f8;
  --map-green:#d7ead0;
  --map-road:#cfd8dc;
}
*{box-sizing:border-box;margin:0;padding:0}
html,body{width:1200px;height:1137px;overflow:hidden}
body{background:var(--page-bg);font-family:"Inter",Arial,sans-serif;color:var(--ink);position:relative}
.page-header{position:absolute;left:0;top:0;width:1200px;height:726px;background:var(--surface)}
.cover{position:absolute;left:0;top:0;width:1200px;height:444px;
  background:linear-gradient(120deg,var(--brand-gold) 0%,var(--brand-olive) 22%,var(--foam) 40%,#c9d4cf 55%,var(--brand-orange) 72%,var(--brand-blue) 86%,var(--foam) 100%)}
.cover-name{position:absolute;left:290px;top:170px;width:250px;height:100px;background:var(--surface);border-radius:8px;display:flex;align-items:center;justify-content:center;color:var(--brand-navy);font-size:24px;font-weight:600}
.avatar{position:absolute;left:48px;top:424px;width:172px;height:172px;border-radius:50%;background:var(--foam);border:5px solid var(--surface);display:flex;align-items:center;justify-content:center;text-align:center;padding:0 20px;color:var(--brand-navy);font-size:20px;font-weight:600;line-height:1.2}
.page-title{position:absolute;left:251px;top:476px;font-size:34px;font-weight:700;line-height:1.22;width:460px}
.page-meta{position:absolute;left:251px;top:564px;font-size:20px;color:var(--ink-soft);line-height:28px}
.page-meta .star{color:#f7b928}
.watch-btn{position:absolute;left:763px;top:561px;width:397px;height:51px;background:var(--action);border-radius:7px;color:#fff;font-size:21px;font-weight:600;display:flex;align-items:center;justify-content:center;gap:10px}
.watch-link{position:absolute;left:897px;top:617px;font-size:17px;color:var(--ink-soft);display:flex;align-items:center;gap:14px}
.header-rule{position:absolute;left:42px;top:649px;width:1117px;height:1px;background:var(--rule)}
.tabs{position:absolute;left:42px;top:666px;height:60px;display:flex}
.tab{font-size:20px;font-weight:500;color:var(--ink-soft);padding:0 20px;height:60px;line-height:44px}
.tab.is-active{color:var(--action);border-bottom:4px solid var(--action)}
.more-btn{position:absolute;left:1100px;top:666px;width:60px;height:43px;background:var(--chip);border-radius:7px;display:flex;align-items:center;justify-content:center;gap:4px}
.more-btn i{width:6px;height:6px;border-radius:50%;background:var(--ink)}
.card{position:absolute;background:var(--surface);border-radius:10px;box-shadow:0 1px 2px rgba(0,0,0,.15)}
.about-card{left:42px;top:746px;width:460px;height:420px}
.card-title{position:absolute;left:20px;top:20px;font-size:24px;font-weight:700}
.see-all{position:absolute;right:20px;top:26px;font-size:19px;color:var(--link)}
.map{position:absolute;left:20px;top:72px;width:419px;height:213px;border-radius:8px;border:1px solid var(--rule);
  background:linear-gradient(100deg,var(--map-green) 0%,#e9efe6 45%,var(--map-road) 70%,#e9efe6 100%)}
.map-pin{position:absolute;left:345px;top:232px}
.address-box{position:absolute;left:48px;top:100px;width:332px;height:79px;background:var(--surface);border-radius:8px;box-shadow:0 1px 4px rgba(0,0,0,.2);display:flex;align-items:center;gap:16px;padding:0 18px}
.address-box p{font-size:18px;color:var(--link);line-height:26px}
.about-text{position:absolute;left:20px;top:318px;width:420px;display:flex;gap:14px;font-size:19px;line-height:27px}
.post-card{left:522px;top:746px;width:638px;height:420px;overflow:hidden}
.post-avatar{position:absolute;left:20px;top:16px;width:48px;height:48px;border-radius:50%;background:var(--foam);border:1px solid var(--rule);display:flex;align-items:center;justify-content:center}
.post-avatar span{width:24px;height:24px;border-radius:50%;background:var(--brand-blue)}
.post-author{position:absolute;left:80px;top:18px;font-size:19px;font-weight:600}
.post-time{position:absolute;left:80px;top:44px;font-size:16px;color:var(--ink-soft);display:flex;align-items:center;gap:5px}
.post-body{position:absolute;left:20px;top:78px;width:610px;font-size:18px;line-height:25.5px;letter-spacing:-.1px}
.post-body p+p{margin-top:8px}
.post-photo{position:absolute;left:0;top:224px;width:638px;height:200px;background:linear-gradient(90deg,#c9c6bd 0%,#e3e1db 40%,#d8d4ca 100%)}
</style>
</head>
<body>
<header class="page-header">
  <div class="cover" role="img" aria-label="Cover collage of foam packaging, recycled beads, volunteers and products"></div>
  <div class="cover-name">FoamLoop Alliance</div>
  <div class="avatar">FoamLoop Alliance</div>
  <h1 class="page-title">FoamLoop Recycling Hub</h1>
  <div class="page-meta">
    <div>@FoamLoopHub · <span class="star">★</span> 4.5 16 reviews ⓘ ·</div>
    <div>Environmental conservation organisation</div>
  </div>
  <div class="watch-btn">
    <svg width="22" height="16" viewBox="0 0 22 16"><rect width="22" height="16" rx="4" fill="#fff"/><path d="M9 4.5v7l6-3.5z" fill="#1b74e4"/></svg>
    Watch Video
  </div>
  <div class="watch-link">
    <svg width="18" height="18" viewBox="0 0 18 18" fill="none" stroke="#65676b" stroke-width="2"><path d="M7 2H2v14h14v-5"/><path d="M10 2h6v6M16 2L8 10"/></svg>
    videoloop.net
  </div>
  <div class="header-rule"></div>
  <nav class="tabs">
    <span class="tab is-active">Home</span>
    <span class="tab">About</span>
    <span class="tab">Events</span>
    <span class="tab">Photos</span>
    <span class="tab">More ▾</span>
  </nav>
  <div class="more-btn"><i></i><i></i><i></i></div>
</header>

<section class="card about-card">
  <h2 class="card-title">About</h2>
  <span class="see-all">See all</span>
  <div class="map" role="img" aria-label="Street map around the office location"></div>
  <svg class="map-pin" width="26" height="34" viewBox="0 0 26 34"><path d="M13 0C6 0 0 6 0 13c0 9 13 21 13 21s13-12 13-21C26 6 20 0 13 0z" fill="#e41e3f"/><circle cx="13" cy="13" r="5" fill="#fff"/></svg>
  <div class="address-box">
    <svg width="18" height="24" viewBox="0 0 18 24"><path d="M9 0C4 0 0 4 0 9c0 6 9 15 9 15s9-9 9-15c0-5-4-9-9-9z" fill="#65676b"/><circle cx="9" cy="9" r="3.5" fill="#fff"/></svg>
    <p>740 Harbor Mill Rd, Ste 12<br>Linwood, MD, US 21090</p>
  </div>
  <div class="about-text">
    <svg width="24" height="24" viewBox="0 0 24 24" style="flex:none;margin-top:2px"><circle cx="12" cy="12" r="12" fill="#65676b"/><rect x="10.5" y="10" width="3" height="8" fill="#fff"/><circle cx="12" cy="6.5" r="1.8" fill="#fff"/></svg>
    <p>Always updating with info on EPS recycling &amp; the industry, the FoamLoop Alliance is a trade association that</p>
  </div>
</section>

<article class="card post-card">
  <div class="post-avatar"><span></span></div>
  <div class="post-author">FoamLoop Recycling Hub</div>
  <div class="post-time">20 h ·
    <svg width="14" height="14" viewBox="0 0 14 14" fill="none" stroke="#65676b" stroke-width="1.4"><circle cx="7" cy="7" r="6"/><path d="M1 7h12M7 1c3 3 3 9 0 12M7 1c-3 3-3 9 0 12"/></svg>
  </div>
  <div class="post-body">
    <p>Great details about the polystyrene recycling operation in Edmonton, Alberta, Canada<br>– this article discusses how they recycle EPS &amp; the collection process,<br>as well as what happens with the recycled foam!</p>
    <p>Click below to find out more:</p>
  </div>
  <div class="post-photo" role="img" aria-label="Recycling plant worker beside stacked bales of white foam"></div>
</article>
</body>
</html>
```